Executive Business Card for Healthcare Company [Need Today]

I need a business card design for a healthcare company. The only branding the company has thus far is a logo. The cards will be utilized by company executives. The design I envision will be vibrant and appealing but with a corporate feel. They shouldn't be too casual or playful. I would like to complete this project TODAY if possible.

Target Market(s)

Healthcare vendors, other executives in healthcare and pharmaceuticals

Industry/Entity Type

Pharmaceutical

Contact Information for Business Card

See attachment

Font styles to use
Serif
Sans Serif

Colors

Designer to choose colors to be used in the design.

```html
<!DOCTYPE html>
<html lang="en">
<head>
<meta charset="utf-8">
<title>Velquen Therapeutics – Business Card</title>
<link rel="stylesheet" href="https://fonts.googleapis.com/css2?family=Crimson+Text:wght@400&family=Open+Sans:wght@300;400&display=swap">
<style>
  :root {
    --page-bg: #8ea7ad;
    --card-bg: #ffffff;
    --teal: #2bbfc6;
    --green: #5cc08d;
    --ink: #1f1f1f;
    --icon-dark: #262a2b;
    --grey-line: #a9a9a9;
    --faint: #ececec;
    --faint-back: #d4d4d4;
    --social-1: #3b5a9a;
    --social-2: #d8477a;
    --social-3: #1a7ab6;
    --social-4: #2aa3ef;
  }
  * { margin: 0; padding: 0; box-sizing: border-box; }
  html, body { width: 1200px; height: 800px; overflow: hidden; }
  body { background: var(--page-bg); position: relative; font-family: "Open Sans", sans-serif; }

  .card {
    position: absolute;
    left: 326px;
    width: 538px;
    height: 307px;
    background: var(--card-bg);
    overflow: hidden;
  }
  .card--front { top: 24px; }
  .card--back { top: 426px; }

  .faint-ring { position: absolute; border-radius: 50%; }
  .card--front .faint-ring {
    left: -46px; top: 32px; width: 304px; height: 304px;
    border: 8px solid var(--faint);
  }
  .card--back .faint-ring {
    left: 347px; top: 121px; width: 186px; height: 186px;
    border: 7px solid var(--faint-back);
  }
  .faint-name {
    position: absolute; left: 318px; top: 188px;
    font-family: "Open Sans", sans-serif; font-weight: 300;
    font-size: 90px; line-height: 1; color: var(--faint);
    white-space: nowrap;
  }

  .brand { position: absolute; display: flex; align-items: center; }
  .brand__ring { border-radius: 50%; border-style: solid; border-color: var(--green); flex: none; }
  .brand__divider { width: 1px; background: var(--grey-line); flex: none; }
  .brand__name {
    font-family: "Open Sans", sans-serif; font-weight: 300;
    color: var(--teal); line-height: 1; text-align: right;
  }
  .brand__name span { display: block; }

  .card--front .brand { left: 68px; top: 50px; }
  .card--front .brand__ring { width: 130px; height: 130px; border-width: 5px; }
  .card--front .brand__divider { height: 66px; margin: 0 12px 0 15px; }
  .card--front .brand__word { font-size: 64px; letter-spacing: 0.5px; }
  .card--front .brand__sub { font-size: 28px; margin-top: 2px; }

  .card--back .brand { left: 296px; top: 24px; }
  .card--back .brand__ring { width: 70px; height: 70px; border-width: 3px; }
  .card--back .brand__divider { height: 40px; margin: 0 7px 0 9px; }
  .card--back .brand__word { font-size: 34px; }
  .card--back .brand__sub { font-size: 16px; margin-top: 1px; }

  .find-us {
    position: absolute; left: 0; width: 538px; top: 200px;
    text-align: center;
    font-family: "Crimson Text", serif; font-size: 17px; color: var(--ink);
  }
  .social { display: flex; justify-content: center; gap: 7px; margin-top: 6px; transform: translateX(-2px); }
  .social__slot { width: 17px; height: 17px; border-radius: 2px; }
  .social__slot:nth-child(1) { background: var(--social-1); }
  .social__slot:nth-child(2) { background: var(--social-2); }
  .social__slot:nth-child(3) { background: var(--social-3); }
  .social__slot:nth-child(4) { background: var(--social-4); border-radius: 50%; }

  .web {
    position: absolute; left: 0; width: 538px; text-align: center;
    font-family: "Crimson Text", serif; font-size: 14px;
  }
  .card--front .web { top: 283px; color: var(--teal); }
  .card--back .web { top: 287px; color: var(--ink); transform: translateX(-4px); }

  .person { position: absolute; left: 27px; top: 24px; font-family: "Crimson Text", serif; color: var(--ink); }
  .person__name { font-size: 41px; line-height: 1; font-weight: 400; }
  .person__title { font-size: 19px; margin-top: 6px; }

  .contact { position: absolute; left: 26px; top: 119px; list-style: none; }
  .contact__item { display: flex; align-items: center; height: 26px; margin-bottom: 13px; }
  .contact__icon { width: 26px; height: 26px; flex: none; }
  .contact__text { margin-left: 11px; font-size: 18px; color: var(--ink); }
  .contact__item--address { align-items: flex-start; margin-top: 4px; }
  .contact__item--address .contact__text {
    margin-left: 5px; margin-top: 2px; font-family: "Crimson Text", serif; font-size: 16px; line-height: 20px;
  }

  .band { position: absolute; top: 293px; height: 6px; background: linear-gradient(90deg, var(--teal), var(--green)); }
  .band--left { left: 0; width: 190px; }
  .band--right { left: 346px; width: 192px; }
</style>
</head>
<body>

<section class="card card--front" aria-label="Business card front">
  <div class="faint-ring"></div>
  <div class="faint-name" aria-hidden="true">velquen</div>

  <div class="brand">
    <div class="brand__ring"></div>
    <div class="brand__divider"></div>
    <div class="brand__name"><span class="brand__word">velquen</span><span class="brand__sub">therapeutics</span></div>
  </div>

  <div class="find-us">
    <p>Find Us on:</p>
    <div class="social" aria-label="Social channels">
      <span class="social__slot"></span><span class="social__slot"></span><span class="social__slot"></span><span class="social__slot"></span>
    </div>
  </div>

  <p class="web">www.website.com</p>
</section>

<section class="card card--back" aria-label="Business card back">
  <div class="faint-ring"></div>

  <div class="person">
    <h1 class="person__name">Daniel Marsh</h1>
    <p class="person__title">Senior Director of Marketing</p>
  </div>

  <div class="brand">
    <div class="brand__ring"></div>
    <div class="brand__divider"></div>
    <div class="brand__name"><span class="brand__word">velquen</span><span class="brand__sub">therapeutics</span></div>
  </div>

  <ul class="contact">
    <li class="contact__item">
      <svg class="contact__icon" viewBox="0 0 26 26" aria-hidden="true">
        <circle cx="13" cy="13" r="13" fill="var(--icon-dark)"/>
        <path d="M9 6.5c.6-.4 1.3-.2 1.6.4l1.2 2.3c.3.6.1 1.2-.4 1.6l-.9.6c.7 1.6 1.900 2.9 3.4 3.8l.7-.8c.4-.5 1.1-.6 1.6-.3l2.2 1.3c.6.3.7 1.1.3 1.6l-.9 1.2c-.6.7-1.6 1-2.5.7-3.7-1.3-6.5-4.3-7.6-8.1-.3-.9.1-1.9.8-2.4z" fill="#fff"/>
      </svg>
      <span class="contact__text">555-014-2276</span>
    </li>
    <li class="contact__item">
      <svg class="contact__icon" viewBox="0 0 26 26" aria-hidden="true">
        <circle cx="13" cy="13" r="13" fill="var(--icon-dark)"/>
        <path d="M6 10c0-2 14-2 14 0v1.5h-3.2v-1.4H9.2v1.4H6z" fill="#fff"/>
        <path d="M9.5 12h7l2 6h-11z" fill="#fff"/>
        <g fill="var(--icon-dark)"><rect x="11" y="13.5" width="1.2" height="1.2"/><rect x="13" y="13.5" width="1.2" height="1.2"/><rect x="15" y="13.5" width="1.2" height="1.2"/><rect x="11" y="15.5" width="1.2" height="1.2"/><rect x="13" y="15.5" width="1.2" height="1.2"/><rect x="15" y="15.5" width="1.2" height="1.2"/></g>
      </svg>
      <span class="contact__text">555-018-6630</span>
    </li>
    <li class="contact__item">
      <svg class="contact__icon" viewBox="0 0 26 26" aria-hidden="true">
        <circle cx="13" cy="13" r="13" fill="var(--icon-dark)"/>
        <rect x="6.5" y="8.5" width="13" height="9" fill="#fff"/>
        <path d="M6.5 8.8l6.5 5 6.5-5M6.5 17.2l5-4.2M19.5 17.2l-5-4.2" stroke="var(--icon-dark)" stroke-width="1" fill="none"/>
      </svg>
      <span class="contact__text">dmarsh@velquenrx.com</span>
    </li>
    <li class="contact__item contact__item--address">
      <svg class="contact__icon" viewBox="0 0 26 26" aria-hidden="true">
        <circle cx="13" cy="13" r="13" fill="var(--icon-dark)"/>
        <path d="M13 5.5a5 5 0 0 1 5 5c0 3.6-5 9.5-5 9.5s-5-5.9-5-9.5a5 5 0 0 1 5-5z" fill="#fff"/>
        <circle cx="13" cy="10.5" r="1.9" fill="var(--icon-dark)"/>
      </svg>
      <span class="contact__text">118 N Harbor Street Easton<br>GA 30699</span>
    </li>
  </ul>

  <div class="band band--left"></div>
  <p class="web">www.website.com</p>
  <div class="band band--right"></div>
</section>

</body>
</html>
```